Visitenkarten für Finanzberater
Zielgruppe
Ich bin Finanzberater und vermittle seit 28 Jahren Versicherungen, Geldanlagen und Finanzierungen. Meine Zielgruppe würde ich als „gehoben“ ansehen, viele haben leitende Positionen, sind Freiberufler, Akademiker ...
Für mich ist der ganzheitliche Beratungsansatz (alles aus einer Hand / ein Ansprechpartner für alle finanziellen Angelegenheiten) sehr wichtig, daher betreue ich viele Kunden schon 20 Jahre und länger.
Derzeit bin ich 57 Jahre alt, viele meiner Kunden in einem ähnlichen Alter. Viele meiner Kunden sind mit Versicherungen sehr gut ausgestattet, einige haben auch Wohnungseigentum (häufig mit mir finanziert).
Im jetzigen Alter ist jedenfalls Geldanlage / Vermögensplanung stark im Vordergrund und genau darauf möchte ich mein neues Visitenkartendesign ausrichten. Im Detail geht es mir um SACHWERT-Veranlagungen, weil aus meiner Sicht unfassbar viel Geld auf unverzinsten Sparkonten von der Inflation aufgefressen werden. Ziel meiner Kunden sollte es sein, mit Sachwertveranlagungen Erträge über der Inflation zu erzielen.
Ich habe laienhafte Graphiken hochgeladen, damit Sie einen ersten Eindruck bekommen.
Die Visitenkarte zeigt aus meiner sich von links nach rechts das gesamte „Kundenleben“.
Ganz links (egal ob das die Geburt oder der Einstieg ins Berufsleben ist) sind Versicherungen sehr wichtig, Der Vermögensaufbau startet ...
Wenn man auf der „Zeitachse“ Richtung Mitte geht, gehen Versicherungsthemen tendenziell zurück, Geldanlagen bleiben gleich breit / wichtig und das Finanzieren einer Immobilie könnte dazukommen.
Mit zunehmendem Alter (auf der Zeitachse weiter nach rechts) rücken Versicherungsthemen immer weiter in den Hintergrund ...
Botschaft meinerseits: Geldanlage (und hier v.a. Sachwertanlagen) sind das ganze Leben lang „gleich wichtig“ und damit kann ich Studenten genauso wie Berufstätige oder Pensionisten sehr gut ansprechen.
In Versicherungsangelegenheiten arbeite ich mit der KOLBIN GmbH ..
Aufgabenstellung
Folgende Inhalte müssen jedenfalls irgendwo auf der Visitenkarte (vorne oder hinten) zu finden sein:
Bereits bestehendes Logo
Mag. iur. Stefan Ortlieb
GF der Ortlieb & Partner GmbH
Finanzberater
Lindenhofweg 58, 8045 Graz
LG für ZRS Graz, FN 713528k
stefan.ortlieb@ortliebkanzlei-beispiel.at
www.ortliebkanzlei-beispiel.at
REVA 48271563 und 26590417
Abfrage REVA: www.reva-register-beispiel.at/versicherungsvermittlerregister
Korrekter wäre es so, aber das ist halt sehr viel Text:
REVA:
26590417 (Gewerbliche Vermögensberatung ohne Berechtigung zur Vermittlung von Lebens- und Unfallversicherungen & Berechtigung zur Tätigkeit als ungebundener Kreditvermittler)
48271563 (Versicherungsvermittlung in der Form Mehrfach-Versicherungsagent in Kooperation mit der KOLBIN GmbH
Die Visitenkarte soll eine 'typische' Größe haben, ich glaube das ist 8,5 x 5,5 cm?
Das Design sollte aufgrund der Klientel schon 'sehr gehoben' sein.
Ergänzend möchte ich erwähnen, dass ich meine Homepage und den Netzwerkly-Banner / Header auf das neue Design anpassen möchte, vielleicht kann letzterer nach Fertigstellung der Visitenkarte bitte mit angeboten werden!?

```html
<!DOCTYPE html>
<html lang="de">
<head>
<meta charset="utf-8">
<title>Visitenkarte – Ortlieb & Partner GmbH</title>
<link rel="stylesheet" href="https://fonts.googleapis.com/css2?family=Roboto:ital,wght@0,300;0,400;0,500;0,700;0,900;1,400&display=swap">
<style>
  :root {
    --bg: #6e6e6e;
    --paper: #ffffff;
    --brand-red: #97142a;
    --brand-blue: #174f6e;
    --brand-grey: #898b8d;
    --name-blue: #1d4f73;
    --ink: #2a2a2a;
    --on-dark: #ffffff;
  }
  * { margin: 0; padding: 0; box-sizing: border-box; }
  html, body { width: 1200px; height: 2400px; overflow: hidden; }
  body {
    background: var(--bg);
    font-family: "Roboto", Arial, sans-serif;
    position: relative;
  }
  .card {
    position: absolute;
    left: 100px;
    width: 1000px;
    height: 648px;
    overflow: hidden;
    box-shadow: 0 4px 14px rgba(0,0,0,0.25);
  }
  .card--front { top: 420px; background: var(--paper); }
  .card--back { top: 1240px; }

  /* front: header */
  .front__head { position: absolute; left: 0; top: 0; width: 100%; height: 340px; background: var(--paper); }
  .brand {
    position: absolute; left: 50px; top: 120px; width: 360px;
    display: flex; flex-direction: column; align-items: center; gap: 18px;
  }
  .brand__mark { width: 70px; height: 70px; background: var(--brand-red); }
  .brand__name {
    font-weight: 500; font-size: 36px; letter-spacing: 1px;
    color: var(--brand-red); white-space: nowrap;
  }
  .person { position: absolute; right: 40px; top: 128px; text-align: right; }
  .person__name { font-size: 42px; font-weight: 500; color: var(--name-blue); line-height: 1.1; }
  .person__role { font-size: 28px; font-weight: 400; color: var(--ink); margin-top: 6px; }
  .person__title { font-size: 28px; font-style: italic; color: var(--ink); margin-top: 20px; }

  .front__stripe { position: absolute; left: 0; top: 340px; width: 100%; height: 21px; background: var(--brand-red); }
  .front__contact {
    position: absolute; left: 0; top: 361px; width: 100%; height: 287px;
    background: var(--brand-blue); color: var(--on-dark);
    font-size: 26px; font-weight: 300; line-height: 35px;
  }
  .contact-list { position: absolute; left: 22px; top: 22px; list-style: none; }
  .contact-list li { display: flex; align-items: flex-start; margin-bottom: 6px; }
  .contact-list .icon { width: 24px; height: 24px; margin: 6px 12px 0 0; flex: none; fill: var(--on-dark); }
  .register { position: absolute; left: 550px; top: 22px; display: flex; }
  .register .icon { width: 22px; height: 24px; margin: 5px 12px 0 0; flex: none; fill: var(--on-dark); }

  .card--back svg { display: block; }
  .band-title { font-weight: 900; font-size: 39px; fill: var(--on-dark); }
  .item { font-size: 31px; font-weight: 300; fill: var(--on-dark); }
  .item--strong { font-weight: 700; }
</style>
</head>
<body>

<section class="card card--front" aria-label="Vorderseite">
  <header class="front__head">
    <div class="brand">
      <span class="brand__mark"></span>
      <span class="brand__name">ORTLIEB &amp; PARTNER</span>
    </div>
    <div class="person">
      <h1 class="person__name">Mag. iur. Stefan Ortlieb</h1>
      <p class="person__role">GF der Ortlieb &amp; Partner GmbH</p>
      <p class="person__title">Finanzberater</p>
    </div>
  </header>
  <div class="front__stripe"></div>
  <div class="front__contact">
    <ul class="contact-list">
      <li>
        <svg class="icon" viewBox="0 0 24 24"><path d="M12 1a8 8 0 0 0-8 8c0 6 8 14 8 14s8-8 8-14a8 8 0 0 0-8-8zm0 11a3 3 0 1 1 0-6 3 3 0 0 1 0 6z"/></svg>
        <span>Lindenhofweg 58, 8045 Graz<br>LG für ZRS Graz, FN 713528k</span>
      </li>
      <li>
        <svg class="icon" viewBox="0 0 24 24"><path d="M6.6 10.8a15 15 0 0 0 6.6 6.6l2.2-2.2c.3-.3.7-.4 1-.2 1.1.4 2.3.6 3.6.6.6 0 1 .4 1 1V20c0 .6-.4 1-1 1A17 17 0 0 1 3 4c0-.6.4-1 1-1h3.5c.6 0 1 .4 1 1 0 1.3.2 2.5.6 3.6.1.3 0 .7-.2 1z"/></svg>
        <span>+43 650 4182936</span>
      </li>
      <li>
        <svg class="icon" viewBox="0 0 24 24"><path d="M2 6h20v12H2z M2 6l10 7 10-7" fill="none" stroke="#fff" stroke-width="0"/><path d="M2 7l10 6 10-6V6H2zm0 2.5V18h20V9.5l-10 6z"/></svg>
        <span>stefan.ortlieb@ortliebkanzlei-beispiel.at</span>
      </li>
      <li>
        <svg class="icon" viewBox="0 0 24 24"><circle cx="12" cy="12" r="9" fill="none" stroke="#fff" stroke-width="2"/><path d="M3 12h18M12 3c3 3 3 15 0 18M12 3c-3 3-3 15 0 18" fill="none" stroke="#fff" stroke-width="1.6"/></svg>
        <span>www.kolbin-beispiel.at/graz-andritz<br>www.finvera-beispiel.at/ortlieb</span>
      </li>
    </ul>
    <div class="register">
      <svg class="icon" viewBox="0 0 22 24"><path d="M2 1h12l6 6v16H2z"/><path d="M14 1v6h6" fill="#174f6e"/></svg>
      <span>REVA 48271563 und 26590417<br>Abfrage REVA:<br>www.reva-register-beispiel.at/<br>versicherungsvermittlerregister</span>
    </div>
  </div>
</section>

<section class="card card--back" aria-label="Rückseite">
  <svg width="1000" height="648" viewBox="0 0 1000 648">
    <defs>
      <g id="tick">
        <circle cx="0" cy="-10" r="10" fill="none" stroke="#fff" stroke-width="2.6"/>
        <path d="M-5 -10 l4 4 l10 -11" fill="none" stroke="#fff" stroke-width="3" stroke-linecap="round"/>
      </g>
    </defs>
    <rect class="band band--grey" width="1000" height="648" fill="#898b8d"/>
    <polygon class="band band--red" points="0,0 1000,0 1000,52 0,318" fill="#97142a"/>
    <polygon class="band band--blue" points="0,602 1000,332 1000,648 0,648" fill="#174f6e"/>

    <g transform="rotate(-15 111 150)"><text class="band-title" x="111" y="150">VERSICHERUNGEN</text></g>
    <g transform="translate(99 228) rotate(-15)"><use href="#tick"/><text class="item" x="20" y="0">Sachwerte</text></g>
    <g transform="translate(321 168) rotate(-15)"><use href="#tick"/><text class="item" x="20" y="0">Humankapital</text></g>

    <g transform="rotate(-15 258 311)"><text class="band-title" x="258" y="311">Sachwert-INVESTITIONEN</text></g>
    <g transform="translate(129 416) rotate(-15)"><use href="#tick"/><text class="item" x="20" y="0">Immobilien</text></g>
    <g transform="translate(349 353) rotate(-15)"><use href="#tick"/><text class="item item--strong" x="18" y="0">Technologiemetalle</text></g>
    <g transform="translate(454 384) rotate(-15)"><use href="#tick"/><text class="item" x="18" y="0">Seltene Erden</text></g>
    <g transform="translate(701 314) rotate(-15)"><use href="#tick"/><text class="item item--strong" x="18" y="0">Venture Capital</text></g>
    <g transform="translate(568 412) rotate(-15)"><use href="#tick"/><text class="item item--strong" x="20" y="0">Aktien</text></g>
    <g transform="translate(358 468) rotate(-15)"><use href="#tick"/><text class="item" x="20" y="0">Edelsteine</text></g>
    <g transform="translate(92 538) rotate(-15)"><use href="#tick"/><text class="item item--strong" x="20" y="0">Private Equity</text></g>

    <g transform="rotate(-15 517 535)"><text class="band-title" x="517" y="535">FINANZIERUNGEN</text></g>
    <g transform="translate(489 608) rotate(-15)"><use href="#tick"/><text class="item" x="20" y="0">Privater Wohnbau</text></g>
    <g transform="translate(811 517) rotate(-15)"><use href="#tick"/><text class="item" x="20" y="0">Leasing</text></g>
  </svg>
</section>

</body>
</html>
```